Calloway Metal Recyclers - www.callowayrecyclers-example.com.au

I've just rebranded my business and thought what better way to continue with this than getting a website.
It is going to be fairly basic for now. I've attached quite a few images, feel free to use whichever you like.
And pages description is also attached in a .doc file.
Updates

Hi, this is my first time having a website. I am open to anything and trust the experience and ideas you can bring forward. I will look at extending the deadline so I can take my time to give feedback as needed! Thank you all.

Target Market(s)

Mining and industrial and commercial sectors

Coding

Coded - Design and coding required

Number of Pages Required

5+ page

Requirements
Must have
• Logo/Phone number at the top of every page. "Scrap Metal Specialists" tag line at the top of every page.
Nice to have
• Top Navigation.

```html
<!DOCTYPE html>
<html lang="en">
<head>
<meta charset="utf-8">
<title>Calloway Metal Recyclers</title>
<link href="https://fonts.googleapis.com/css2?family=Abril+Fatface&family=Open+Sans:wght@400;600;700;800&family=Ultra&display=block" rel="stylesheet">
<style>
:root{
  --navy:#1b3a6f;
  --ink:#222;
  --muted:#555;
  --white:#fff;
  --black:#000;
  --line:#8a8a8a;
  --hero-top:#2c3350;
  --hero-mid:#5d5445;
  --hero-low:#7a6236;
}
*{margin:0;padding:0;box-sizing:border-box}
html,body{width:1200px;height:2990px;overflow:hidden;background:var(--white)}
body{font-family:"Open Sans",Arial,sans-serif;color:var(--ink)}
.page{position:relative;width:1200px;height:2990px;overflow:hidden}
.abs{position:absolute}
.display{font-family:"Ultra","Abril Fatface","Rockwell Extra Bold","Georgia",serif;font-weight:900;font-synthesis:none;color:var(--navy);letter-spacing:1px}
ul{list-style:none}

/* top bar */
.topbar{left:528px;top:0;width:672px;height:32px;background:var(--navy);clip-path:polygon(0 0,100% 0,100% 100%,38px 100%);color:var(--white);font-size:13px;display:flex;align-items:center;gap:34px;padding-left:76px}
.topbar span{display:flex;align-items:center;gap:6px}
.topbar .social{display:flex;gap:8px;margin-left:14px;font-size:10px}
.topbar .social i{font-style:normal;border:1px solid #fff;border-radius:10px;padding:0 5px;line-height:16px}

.brand{left:111px;top:24px;width:250px;font-weight:800;font-size:18px;line-height:22px;color:var(--navy);white-space:nowrap}
.brand .tagline{display:block;font-size:12px;line-height:18px;font-weight:600;color:#666;letter-spacing:.5px;text-transform:uppercase}
.brand .phone{display:block;font-size:16px;line-height:20px;font-weight:700;color:#666}

.nav{left:417px;top:62px;display:flex;gap:40px;font-size:16px;color:#444}
.nav .current{color:var(--ink);font-weight:600}
.btn-login{left:976px;top:52px;width:113px;height:42px;background:var(--navy);color:var(--white);font-weight:700;font-size:15px;display:flex;align-items:center;justify-content:center}

/* hero */
.hero{left:0;top:114px;width:1200px;height:640px;clip-path:polygon(0 0,100% 0,100% 505px,50% 640px,0 505px);
  background:radial-gradient(circle at 28% 12%,#c9ccd6 0,#6b7088 10%,transparent 28%),linear-gradient(180deg,var(--hero-top) 0%,#41445a 28%,var(--hero-mid) 55%,var(--hero-low) 100%)}
.hero-text{left:0;top:298px;width:1200px;text-align:center;color:var(--white)}
.hero-text .kicker{font-size:30px;margin-bottom:6px}
.hero-text h1{color:var(--white);font-size:76px;line-height:90px}
.dots{left:568px;top:723px;display:flex;gap:12px}
.dots i{width:13px;height:4px;background:#bbb;border-radius:2px}
.dots i+i{background:#fff}

/* services */
.section-title{left:0;width:1200px;text-align:center;font-size:38px;line-height:50px}
.svc{top:961px;width:308px;height:412px;background:var(--white);box-shadow:0 0 10px rgba(0,0,0,.12)}
.svc .photo{position:absolute;left:17px;top:14px;width:274px;height:343px}
.svc .label{position:absolute;left:22px;top:368px;width:265px;height:58px;background:var(--navy);color:var(--white);font-size:18px;display:flex;align-items:center;justify-content:center}

/* about */
.about{left:0;top:1498px;width:1200px;height:464px;background:linear-gradient(100deg,#1c3c72 0%,#3f5682 42%,#8b8e95 100%);overflow:hidden}
.about h2{left:111px;top:90px;font-size:38px;line-height:50px;color:var(--white)}
.about p{left:111px;top:166px;width:502px;font-size:15.5px;line-height:30px;color:var(--white);text-align:justify}
.about .btn-outline{left:111px;top:317px;width:113px;height:42px;border:2px solid #fff;color:#fff;font-weight:700;font-size:15px;display:flex;align-items:center;justify-content:center}
.sheet{width:320px;height:330px}

/* blog */
.post{top:2125px;width:284px;height:315px;background:var(--white);box-shadow:0 0 10px rgba(0,0,0,.1);border-bottom:4px solid var(--line);padding:26px 22px 0 22px}
.post .date{font-size:15px;color:#666;margin-left:3px}
.post h3{font-size:20.5px;font-weight:400;line-height:29px;margin-top:12px}
.post p{font-size:17px;line-height:28px;color:var(--muted);margin-top:13px}
.post .more{display:block;margin-top:14px;margin-left:-3px;font-weight:700;font-size:17px;color:var(--navy)}

/* footer */
.foot-brand{left:111px;top:2712px;width:300px;color:var(--white);font-weight:800;font-size:40px;line-height:46px}
.foot-brand small{display:block;font-size:26px;line-height:32px;font-weight:800}
.follow{left:111px;top:2868px;display:flex;align-items:center;gap:10px;color:#fff;font-size:17px}
.follow i{font-style:normal;width:36px;height:36px;border:1.5px solid #fff;border-radius:50%;font-size:9px;display:flex;align-items:center;justify-content:center}
.col-title{top:2692px;color:#fff;font-size:15px}
.col-list{top:2748px;color:#fff;font-size:13px;line-height:26px}
.col-list li{color:#fff}
.contact{left:481px;top:2748px;color:#fff;font-size:13px}
.contact li{display:flex;gap:14px;margin-bottom:12px;line-height:26px;color:#fff}
.contact svg{flex:none;margin-top:6px}
.rule{left:111px;top:2938px;width:978px;height:1px;background:#444}
.copy{left:0;top:2954px;width:1200px;text-align:center;color:#fff;font-size:14px}
</style>
</head>
<body>
<div class="page">

  <!-- header -->
  <div class="abs topbar">
    <span><svg width="12" height="12" viewBox="0 0 24 24"><path fill="#fff" d="M6.6 10.8a15 15 0 006.6 6.6l2.2-2.2c.3-.3.7-.4 1-.2 1.1.4 2.3.6 3.6.6.6 0 1 .4 1 1V20c0 .6-.4 1-1 1A17 17 0 013 4c0-.6.4-1 1-1h3.5c.6 0 1 .4 1 1 0 1.3.2 2.5.6 3.6.1.3 0 .7-.2 1z"/></svg>0491570110</span>
    <span><svg width="13" height="13" viewBox="0 0 24 24"><path fill="#fff" d="M2 12l20-9-7 19-3-8z"/></svg>sam@callowayrecyclers-example.com.au</span>
    <span class="social"><i>Fb</i><i>Tw</i><i>Ig</i></span>
  </div>
  <div class="abs brand">Calloway Metal Recyclers<span class="tagline">Scrap Metal Specialists</span><span class="phone">0491570110</span></div>
  <nav class="abs nav"><span class="current">Home</span><span>About</span><span>Services</span><span>Online Store</span><span>Blog</span><span>Contact</span></nav>
  <div class="abs btn-login">LOGIN</div>

  <!-- hero -->
  <div class="abs hero" role="img" aria-label="Scrap yard at dusk with large steel cable drums, a yellow access stairway and piles of scrap metal"></div>
  <svg class="abs" style="left:0;top:0" width="1200" height="800" viewBox="0 0 1200 800">
    <polygon points="0,619 600,754 1200,619 1200,636 600,783 0,636" fill="#1b3a6f"/>
    <polyline points="174,673 600,762 1026,673" fill="none" stroke="#1b3a6f" stroke-width="3"/>
  </svg>
  <div class="abs hero-text">
    <div class="kicker">WELCOME TO</div>
    <h1 class="display">CALLOWAY METAL<br>RECYCLERS</h1>
  </div>
  <div class="abs dots"><i></i><i></i><i></i></div>

  <!-- services -->
  <h2 class="abs display section-title" style="top:866px">OUR SERVICES</h2>
  <div class="abs svc" style="left:111px">
    <div class="photo" role="img" aria-label="Large rusted steel shaft cut open on a scrap heap" style="background:linear-gradient(160deg,#8a5a3e,#6b4a38 50%,#8d9298)"></div>
    <div class="label">Large Mining Machinery</div>
  </div>
  <div class="abs svc" style="left:447px">
    <div class="photo" role="img" aria-label="Rusted industrial steel pipe sections cut into rings" style="background:linear-gradient(180deg,#9a8a76,#7b4a36 40%,#5b4a44 100%)"></div>
    <div class="label">Heavy Industrial Equipment</div>
  </div>
  <div class="abs svc" style="left:782px">
    <div class="photo" role="img" aria-label="Rusted steel truck tray waiting for scrap clean up under trees" style="background:linear-gradient(180deg,#a9b4bf 0%,#5f6b4e 30%,#7a4b34 60%,#6b5a48 100%)"></div>
    <div class="label">Scrap Metal Clean Up</div>
  </div>

  <!-- about -->
  <section class="abs about">
    <h2 class="abs display">ABOUT ME</h2>
    <p class="abs">My name is Sam Calloway and I'm the managing director of Calloway Metal Processors. I have been in the scrap metal recycling industry longer than I haven't! I have 16 years' experience in everything scrap metal and I am very passionate about sustainable recycling.</p>
    <div class="abs btn-outline">LOGIN</div>
    <div class="abs sheet" style="left:745px;top:45px;transform:rotate(-24deg);background:#dfe0e4"></div>
    <div class="abs sheet" role="img" aria-label="Portrait of the managing director in a blue blazer against a light backdrop" style="left:740px;top:55px;transform:rotate(-30deg);background:linear-gradient(180deg,#f2f2f3 0%,#e4e5e8 45%,#3a5a8c 70%,#2b4a7a 100%)"></div>
  </section>

  <!-- blog -->
  <h2 class="abs display section-title" style="top:2025px">LATEST BLOG</h2>
  <article class="abs post" style="left:115px"><div class="date">18-11-2022</div><h3>Duis aute irure dolor volt incieri rnderit in volupt.</h3><p>Duis aute irure dolor voltter incieri rnderit in volupt. Cillt dolore eu fugiat nulla loreti pariatur.</p><span class="more">READ MORE</span></article>
  <article class="abs post" style="left:460px"><div class="date">18-11-2022</div><h3>Duis aute irure dolor volt incieri rnderit in volupt.</h3><p>Duis aute irure dolor voltter incieri rnderit in volupt. Cillt dolore eu fugiat nulla loreti pariatur.</p><span class="more">READ MORE</span></article>
  <article class="abs post" style="left:805px"><div class="date">18-11-2022</div><h3>Duis aute irure dolor volt incieri rnderit in volupt.</h3><p>Duis aute irure dolor voltter incieri rnderit in volupt. Cillt dolore eu fugiat nulla loreti pariatur.</p><span class="more">READ MORE</span></article>

  <!-- footer -->
  <svg class="abs" style="left:0;top:2500px" width="1200" height="490" viewBox="0 2500 1200 490">
    <polyline points="174,2618 600,2526 1026,2618" fill="none" stroke="#1b3a6f" stroke-width="3"/>
    <polygon points="0,2653 600,2511 1200,2653 1200,2672 600,2530 0,2672" fill="#1b3a6f"/>
    <polygon points="0,2672 600,2530 1200,2672 1200,2990 0,2990" fill="#000"/>
  </svg>
  <div class="abs foot-brand">CALLOWAY<small>METAL RECYCLERS<br>0491570110</small></div>
  <div class="abs follow">FOLLOW US: <i>in</i><i>Fb</i><i>Ig</i></div>

  <div class="abs col-title" style="left:481px">CONTACT INFO</div>
  <ul class="abs contact">
    <li><svg width="14" height="16" viewBox="0 0 24 28"><path fill="#fff" d="M12 0a10 10 0 00-10 10c0 7.5 10 18 10 18s10-10.5 10-18A10 10 0 0012 0zm0 14a4 4 0 110-8 4 4 0 010 8z"/></svg><span>Calloway Metal Recycle,<br>Address Comes Here</span></li>
    <li><svg width="14" height="14" viewBox="0 0 24 24"><path fill="#fff" d="M6.6 10.8a15 15 0 006.6 6.6l2.2-2.2c.3-.3.7-.4 1-.2 1.1.4 2.3.6 3.6.6.6 0 1 .4 1 1V20c0 .6-.4 1-1 1A17 17 0 013 4c0-.6.4-1 1-1h3.5c.6 0 1 .4 1 1 0 1.3.2 2.5.6 3.6.1.3 0 .7-.2 1z"/></svg><span>0491570110</span></li>
    <li><svg width="15" height="12" viewBox="0 0 24 18"><path fill="#fff" d="M0 0h24v18H0zm2 2v1l10 7 10-7V2z"/></svg><span>sam@callowayrecyclers-example.com.au</span></li>
  </ul>

  <div class="abs col-title" style="left:784px">QUICK LINKS</div>
  <ul class="abs col-list" style="left:784px"><li>Home</li><li>About</li><li>Services</li><li>Online Store</li><li>Blog</li></ul>

  <div class="abs col-title" style="left:966px">OTHER LINKS</div>
  <ul class="abs col-list" style="left:966px;font-size:14px"><li>Terms &amp; conditions</li><li>Privacy Policy</li><li>Contact Us</li></ul>

  <div class="abs rule"></div>
  <div class="abs copy">©Copyrights 2022 Calloway Metal Recycle. All Rights Reserved.</div>
</div>
</body>
</html>
```